Website Design Request - Management Consulting Firm

We need a Website designed for an IT Management Staffing and Recruiting firm called TRAVENOK based in San Francisco.

The firm is an high-end technology staffing agency. Our focus is on quality and high-caliber candidates rather than quantity.

The website will have two main home pages. One for the recruiter and another on for the candidates.

The website needs to optimize for mobile devices as well.

I have attached few mock-ups that I have done just to show what I am thinking. The UI needs to be very clean, fluid, and it needs to have a modern, rustic, professional feel to it.

Target Market(s)

Technology Manager, Director, VP, CIO of Companies that have $4b-10b dollar revenue. Such as larkspurdwellings.example , https://www.velmorian.example/, quillnet.example, zib.example

Industry/Entity Type

Management Consulting

Number of Pages Required

5+ page

Font styles to use
Sans Serif

Colors
f37122
ffffff

Requirements
Must have
• Please review mock-ups for suggestions
Nice to have
Should not have

```html
<!DOCTYPE html>
<html lang="en">
<head>
<meta charset="utf-8">
<title>TRAVENOK — IT Project Management Jobs</title>
<link href="https://fonts.googleapis.com/css2?family=Lora:wght@400;700&family=Open+Sans:wght@400;600&display=swap" rel="stylesheet">
<style>
:root{
  --orange:#f36b22;
  --white:#ffffff;
  --ink:#222222;
  --muted:#555555;
  --tab-grey:#e2e2e2;
  --footer-bg:#f2f2f2;
  --field-border:#cfcfcf;
  --grey-logo:#9a9a9a;
  --dark-btn:#3a3a3a;
}
*{margin:0;padding:0;box-sizing:border-box}
html,body{width:1064px;height:1200px;overflow:hidden;background:var(--white)}
body{position:relative;font-family:"Open Sans",Arial,sans-serif;color:var(--ink)}
.abs{position:absolute}
.serif{font-family:"Lora",Georgia,serif}

/* header */
.brand{left:117px;top:26px;font-family:"Lora",Georgia,serif;font-size:40px;letter-spacing:1px;color:var(--orange);line-height:1}
.nav{top:44px;font-size:11px;color:var(--ink);white-space:nowrap}
.nav.active{color:var(--orange)}
.nav svg{vertical-align:-1px;margin-right:3px}

/* hero */
.hero{left:0;top:102px;width:1064px;height:442px;background:radial-gradient(ellipse at 60% 40%,#5d4a3b 0%,#3a2f27 45%,#1f1b19 100%)}
.hero-title{left:0;width:1064px;top:216px;text-align:center;font-family:"Lora",Georgia,serif;font-weight:700;font-size:29px;color:var(--white)}
.hero-sub{left:0;width:1064px;top:255px;text-align:center;font-family:"Lora",Georgia,serif;font-size:19px;color:var(--white)}
.email-field{left:354px;top:297px;width:355px;height:38px;background:var(--white);font-family:"Lora",Georgia,serif;font-size:12px;color:#666;padding:12px 17px}
.cta{left:454px;top:350px;width:156px;height:39px;background:var(--orange);color:var(--white);font-family:"Lora",Georgia,serif;font-weight:700;font-size:14px;text-align:center;line-height:39px}
.hero-link{left:0;width:1064px;top:411px;text-align:center;font-size:11px;font-weight:600;color:var(--white)}
.hero-link u{margin-left:6px}
.arrow{top:308px}

/* tabs */
.tab{top:571px;height:43px;width:415px;text-align:center;line-height:43px;font-family:"Lora",Georgia,serif;font-size:19px}
.tab-how{left:116px;background:var(--orange);color:var(--white)}
.tab-why{left:532px;background:var(--tab-grey);color:#333}
.tab-pointer{left:314px;top:614px;width:0;height:0;border-left:9px solid transparent;border-right:9px solid transparent;border-top:10px solid var(--orange)}

.kicker{left:0;width:1064px;top:650px;text-align:center;font-size:11px;color:#333}
.steps-title{left:0;width:1064px;top:671px;text-align:center;font-family:"Lora",Georgia,serif;font-size:19px;color:#222}
.step-line{left:246px;top:745px;width:573px;height:2px;background:#dddddd}
.step-icon{width:42px;height:42px;border-radius:50%;background:var(--orange);top:725px;display:flex;align-items:center;justify-content:center}
.step-title{top:778px;width:300px;text-align:center;font-family:"Lora",Georgia,serif;font-size:14.5px;color:var(--orange)}
.step-text{top:803px;width:260px;text-align:center;font-size:9px;line-height:14px;color:#333}
.outline-btn{left:433px;top:863px;width:198px;height:53px;border:2px solid var(--orange);border-radius:2px;color:var(--orange);font-family:"Lora",Georgia,serif;font-size:15px;display:flex;align-items:center;justify-content:center;gap:7px}

/* footer */
.footer{left:0;top:987px;width:1064px;height:213px;background:var(--footer-bg)}
.f-head{top:1024px;font-family:"Lora",Georgia,serif;font-size:12px;color:#222}
.contact-item{left:118px;font-size:9px;color:#222;display:flex;align-items:center;gap:7px}
.social{top:1143px;width:23px;height:23px;border-radius:50%}
.field{width:170px;height:32px;border:1px solid var(--field-border);background:var(--white);font-size:10px;color:#777;padding:9px 12px}
.submit{left:374px;top:1134px;width:62px;height:32px;background:var(--dark-btn);color:var(--white);font-size:10px;font-weight:600;text-align:center;line-height:32px}
.f-brand{left:788px;top:1026px;font-family:"Lora",Georgia,serif;font-size:26px;letter-spacing:1px;color:var(--grey-logo)}
.copyright{left:788px;top:1066px;font-size:9px;line-height:16px;color:#222}
</style>
</head>
<body>

<header>
  <div class="abs brand">TRAVENOK</div>
  <div class="abs nav active" style="left:675px">Professional</div>
  <div class="abs nav" style="left:758px">Employers</div>
  <div class="abs nav" style="left:832px"><svg width="7" height="9" viewBox="0 0 7 9"><rect x="0" y="4" width="7" height="5" fill="#222"/><path d="M1.5 4V2.5a2 2 0 0 1 4 0V4" stroke="#222" fill="none"/></svg>Sign In</div>
  <div class="abs nav" style="left:898px"><svg width="9" height="9" viewBox="0 0 9 9"><path d="M1 8l1-3 5-5 2 2-5 5z" fill="#222"/></svg>Sign Up</div>
</header>

<section>
  <div class="abs hero" role="img" aria-label="Overhead photo of a team meeting around a wooden table with laptops, papers and coffee"></div>
  <svg class="abs arrow" style="left:20px" width="20" height="30" viewBox="0 0 20 30"><path d="M15 3L4 15l11 12" stroke="#bbb" stroke-width="3" fill="none"/></svg>
  <svg class="abs arrow" style="left:1024px" width="20" height="30" viewBox="0 0 20 30"><path d="M5 3l11 12L5 27" stroke="#bbb" stroke-width="3" fill="none"/></svg>
  <h1 class="abs hero-title">Looking for IT Project&nbsp; Management Jobs?</h1>
  <p class="abs hero-sub">Upload your resume, accept interview requests, get offers</p>
  <div class="abs email-field">Your Email Address</div>
  <div class="abs cta">GET OFFERS NOW</div>
  <p class="abs hero-link">Looking for talents? <u>See how it works for Employers</u></p>
</section>

<section>
  <div class="abs tab tab-how">How it works?</div>
  <div class="abs tab tab-why">Why us?</div>
  <div class="abs tab-pointer"></div>

  <p class="abs kicker">3 Simple Steps</p>
  <h2 class="abs steps-title" style="font-weight:400">Employers pay 25% more for a better FIT Project Manager</h2>

  <div class="abs step-line"></div>
  <div class="abs step-icon" style="left:225px"><svg width="18" height="16" viewBox="0 0 18 16"><path d="M9 0l5 5h-3v5H7V5H4z" fill="#fff"/><rect x="1" y="11" width="16" height="4" fill="#fff"/></svg></div>
  <div class="abs step-icon" style="left:511px"><svg width="20" height="14" viewBox="0 0 20 14"><rect width="20" height="14" rx="1" fill="#fff"/><path d="M1 1l9 7 9-7" stroke="#f36b22" stroke-width="1.6" fill="none"/></svg></div>
  <div class="abs step-icon" style="left:798px"><svg width="20" height="12" viewBox="0 0 20 12"><rect x="1" y="1" width="18" height="10" stroke="#fff" stroke-width="2" fill="none"/><circle cx="10" cy="6" r="3" fill="#fff"/></svg></div>

  <h3 class="abs step-title" style="left:96px;font-weight:400">Upload Your Resume</h3>
  <h3 class="abs step-title" style="left:382px;font-weight:400">We Send You Interview Requests</h3>
  <h3 class="abs step-title" style="left:669px;font-weight:400">Get $1000 Bonus</h3>
  <p class="abs step-text" style="left:116px">Answer few question and upload your resume</p>
  <p class="abs step-text" style="left:402px">Interested in someone? With a single click, send interview request and let us handle the rest</p>
  <p class="abs step-text" style="left:689px">Find a job and get $1000 bonus TRAVENOK</p>

  <div class="abs outline-btn"><svg width="12" height="11" viewBox="0 0 12 11"><path d="M6 0l4 4H8v3H4V4H2z" fill="#f36b22"/><rect y="8" width="12" height="3" fill="#f36b22"/></svg>Upload Your Resume</div>
</section>

<footer>
  <div class="abs footer"></div>
  <h4 class="abs f-head" style="left:118px;font-weight:400">Contact Info</h4>
  <div class="abs contact-item" style="top:1052px"><svg width="7" height="9" viewBox="0 0 7 9"><path d="M3.5 9L0.5 4a3 3 0 1 1 6 0z" fill="#222"/></svg>418 Alder Crest Way, Fremont, CA 94538</div>
  <div class="abs contact-item" style="top:1075px"><svg width="7" height="9" viewBox="0 0 7 9"><rect x="1" y="0.5" width="5" height="8" rx="1" stroke="#222" fill="none"/></svg>Phone : 555 014 2290</div>
  <div class="abs contact-item" style="top:1097px"><svg width="7" height="9" viewBox="0 0 7 9"><rect y="2" width="7" height="5" fill="#222"/></svg>Email: office@travenoktech.example</div>
  <div class="abs social" style="left:118px;background:#3b5998"></div>
  <div class="abs social" style="left:147px;background:#1da1f2"></div>
  <div class="abs social" style="left:176px;background:#0077b5"></div>

  <h4 class="abs f-head" style="left:374px;font-weight:400">Contact Us</h4>
  <div class="abs field" style="left:374px;top:1054px">Name</div>
  <div class="abs field" style="left:551px;top:1054px">Email</div>
  <div class="abs field" style="left:374px;top:1094px">Subject</div>
  <div class="abs field" style="left:551px;top:1094px">Message</div>
  <div class="abs submit">SUBMIT</div>

  <div class="abs f-brand">TRAVENOK</div>
  <p class="abs copyright">Copyright &copy;&nbsp; 2016&nbsp;&nbsp; Company name.<br>All rights reserved.</p>
</footer>

</body>
</html>
```